New Bicycle shop business card

Hi!
I'm looking for a business card for my new proffesional bike mechanics shop. This shop is only for fixing broken bikes and not selling bikes.
Peferbly a modern and sleek and modern design.
Colors: black, grey, red, white
Information:
Name: Rijwielwerkplaats Vanhoutte
Shop owner: Bart Vanhoutte & Marieke Segers
Website: www.rijwielwerkplaats-vanhoutte.be
Email: info@rijwielwerkplaats-vanhoutte.be
Phone number: +32471902368
Street adres: Kerkweg 46
9940 Bellebeke
Slogan/shop information: Herstellingen van alle merken.
Logo: see files.
Target Market(s)
People who seek a mechanic to fix or upgrade their bikes.
Contact Information for Business Card
Information:
Website: info@rijwielwerkplaats-vanhoutte.be
9940 Bellebeke
Logo: see files.

```html
<!DOCTYPE html>
<html lang="nl">
<head>
<meta charset="utf-8">
<title>Rijwielwerkplaats Vanhoutte – Visitekaartje</title>
<link rel="stylesheet" href="https://fonts.googleapis.com/css2?family=Fira+Sans:wght@400;600;700&display=swap">
<style>
  :root {
    --bg: #2b2b2d;
    --card-black: #0c0c0d;
    --card-white: #f6f6f6;
    --red: #e0334f;
    --ink: #1f1f21;
    --grey: #6a6a6d;
    --rule: #3a3a3c;
    --white: #ffffff;
  }
  * { box-sizing: border-box; margin: 0; padding: 0; }
  html, body {
    width: 1200px; height: 900px; overflow: hidden;
    background: var(--bg);
    font-family: "Fira Sans", sans-serif;
  }
  .stage {
    width: 1200px; height: 900px;
    display: flex; flex-direction: column;
    align-items: center; justify-content: center; gap: 48px;
  }
  .card {
    position: relative;
    width: 640px; height: 366px;
    overflow: hidden;
    box-shadow: 0 18px 40px rgba(0,0,0,.45);
  }
  .card::after {
    content: ""; position: absolute; left: 0; right: 0; bottom: 0;
    height: 10px; background: var(--red);
  }
  .card--back { background: var(--card-black); display: flex; align-items: center; justify-content: center; }
  .card--front { background: var(--card-white); }

  .wordmark { display: flex; flex-direction: column; align-items: center; gap: 14px; }
  .wordmark__square { width: 40px; height: 40px; background: var(--red); }
  .wordmark__name {
    font-weight: 700; font-size: 26px; line-height: 1.1;
    text-transform: uppercase; letter-spacing: 1px; text-align: center;
  }
  .card--back .wordmark__name { color: var(--white); }
  .card--front .wordmark__name { color: var(--ink); font-size: 22px; }

  .card--front .wordmark {
    position: absolute; left: 40px; top: 110px; width: 240px;
  }
  .divider {
    position: absolute; left: 304px; top: 80px;
    width: 1px; height: 150px; background: var(--rule);
  }
  .contact {
    position: absolute; left: 326px; top: 72px; width: 300px;
    color: var(--ink);
  }
  .contact__names {
    color: var(--red); font-weight: 700; font-size: 15px;
    text-transform: uppercase; letter-spacing: .2px;
  }
  .contact__role { font-size: 13px; margin-top: 3px; margin-bottom: 14px; }
  .contact__list { list-style: none; }
  .contact__item {
    display: flex; align-items: center; gap: 9px;
    font-size: 13px; line-height: 1; margin-bottom: 8px;
  }
  .contact__item svg { width: 13px; height: 13px; flex: none; fill: var(--red); }
  .contact__address { font-size: 13px; margin-top: 16px; }
  .slogan {
    position: absolute; right: 28px; bottom: 32px;
    color: var(--grey); font-size: 15px;
  }
</style>
</head>
<body>
<main class="stage">
  <section class="card card--back" aria-label="Achterkant visitekaartje">
    <div class="wordmark">
      <span class="wordmark__square"></span>
      <span class="wordmark__name">Rijwielwerkplaats<br>Vanhoutte</span>
    </div>
  </section>

  <section class="card card--front" aria-label="Voorkant visitekaartje">
    <div class="wordmark">
      <span class="wordmark__square"></span>
      <span class="wordmark__name">Rijwielwerkplaats<br>Vanhoutte</span>
    </div>
    <div class="divider"></div>
    <div class="contact">
      <p class="contact__names">Bart Vanhoutte &amp; Marieke Segers</p>
      <p class="contact__role">Shop owner</p>
      <ul class="contact__list">
        <li class="contact__item">
          <svg viewBox="0 0 24 24" aria-hidden="true"><path d="M6.6 10.8a15.1 15.1 0 0 0 6.6 6.6l2.2-2.2c.3-.3.7-.4 1-.2 1.1.4 2.3.6 3.6.6.6 0 1 .4 1 1V20c0 .6-.4 1-1 1C10.6 21 3 13.4 3 4c0-.6.4-1 1-1h3.5c.6 0 1 .4 1 1 0 1.3.2 2.5.6 3.6.1.3 0 .7-.2 1z"/></svg>
          +32471902368
        </li>
        <li class="contact__item">
          <svg viewBox="0 0 24 24" aria-hidden="true"><path d="M2 5h20v14H2zm2 2v.4l8 5.3 8-5.3V7zm0 2.8V17h16V9.8l-8 5.3z"/></svg>
          info@rijwielwerkplaats-vanhoutte.be
        </li>
        <li class="contact__item">
          <svg viewBox="0 0 24 24" aria-hidden="true"><circle cx="12" cy="12" r="10"/></svg>
          www.rijwielwerkplaats-vanhoutte.be
        </li>
      </ul>
      <p class="contact__address">Kerkweg 46, 9940 Bellebeke</p>
    </div>
    <p class="slogan">Herstellingen van alle merken</p>
  </section>
</main>
</body>
</html>
```